RW Holloway LLC Business Card - Civil Engineering & Consulting Firm

We need a Business Card that is elegant, and masculine.  It is our Professional Civil Engineering & Consulting Company located in San Antonio TX (Not s construction or builder firm- no gears & no tool images please). We provide civil engineering services including  commercial site plans, grading and drainage plans, utility plans, hydraulics and hydrology, land planning, utility coordination, and other general civil engineering services related to commercial and residential development.
We have 2 existing Logos. We would like to convey reliability, strength, trustworthiness and attention to detail.  Blues and orange tones as per logo We are OK with the use of a darker blue in the mix.  We have 2 logo versions - Full Company Name Logo to go on the back of card, & Small Icon Logo for the front w/ personal Info.

Target Market(s)
Architects, Real Estate Developers, Other Strctural Engineers, Surveyers, General Contractors
Industry/Entity Type
Professional Civil Engineering
Contact Information for Business Card
Name, Position, Address, Cell & Office #, email, and company website
Font styles to use
Other font styles liked:
- Avian
Requirements
Should not have
- No Tools, No Gears, no Cranes, or Construction Equipment.

```html
<!DOCTYPE html>
<html lang="en">
<head>
<meta charset="utf-8">
<title>RW Holloway LLC – Business Card</title>
<link rel="stylesheet" href="https://fonts.googleapis.com/css2?family=Questrial&display=swap">
<style>
  :root {
    --backdrop: #b9b9b9;
    --card-white: #ffffff;
    --navy: #002447;
    --sky: #7aadd8;
    --orange: #f2922c;
    --ink: #3a3a3a;
  }
  * { margin: 0; padding: 0; box-sizing: border-box; }
  html, body {
    width: 1200px; height: 1200px; overflow: hidden;
    background: var(--backdrop);
    font-family: "Questrial", sans-serif;
  }
  .canvas { position: relative; width: 1200px; height: 1200px; }
  .card {
    position: absolute; left: 262px; width: 686px; height: 392px;
  }
  .card--front { top: 165px; background: var(--card-white); }
  .card--back { top: 653px; background: var(--navy); }

  .front-brand {
    position: absolute; left: 96px; top: 184px;
    display: flex; align-items: center; gap: 8px;
    white-space: nowrap;
  }
  .brand-square { width: 12px; height: 12px; background: var(--orange); flex: none; }
  .front-brand__name { color: var(--sky); font-size: 20px; letter-spacing: 0.5px; line-height: 1; }

  .contact { position: absolute; left: 310px; top: 92px; }
  .contact__name {
    color: var(--sky); font-size: 24px; letter-spacing: 0.3px; line-height: 1;
    -webkit-text-stroke: 0.4px var(--sky);
  }
  .contact__role { color: var(--orange); font-size: 16px; margin-top: 4px; }
  .contact__list { list-style: none; margin-top: 22px; }
  .contact__item {
    display: flex; align-items: center; gap: 16px; margin-bottom: 15px;
    color: var(--ink); font-size: 16.5px; line-height: 20px;
  }
  .contact__icon { width: 21px; height: 24px; flex: none; }

  .back-brand {
    position: absolute; inset: 0;
    display: flex; align-items: center; justify-content: center; gap: 14px;
  }
  .back-brand__name { color: var(--sky); font-size: 46px; letter-spacing: 6px; }
  .back-brand .brand-square { width: 20px; height: 20px; }
</style>
</head>
<body>
<main class="canvas">
  <section class="card card--front" aria-label="Business card front">
    <div class="front-brand">
      <span class="brand-square"></span>
      <span class="front-brand__name">RW Holloway</span>
    </div>
    <div class="contact">
      <h1 class="contact__name">DANIEL REEVES</h1>
      <p class="contact__role">President</p>
      <ul class="contact__list">
        <li class="contact__item">
          <svg class="contact__icon" viewBox="0 0 21 24" aria-hidden="true">
            <rect width="21" height="24" fill="var(--sky)"/>
            <path d="M10.5 5a4 4 0 0 0-4 4c0 3 4 8 4 8s4-5 4-8a4 4 0 0 0-4-4z" fill="none" stroke="#fff" stroke-width="1.5"/>
            <circle cx="10.5" cy="9" r="1.4" fill="#fff"/>
          </svg>
          <span>4120 Cedar Hollow Drive<br>San Antonio, Texas 78209</span>
        </li>
        <li class="contact__item">
          <svg class="contact__icon" viewBox="0 0 21 24" aria-hidden="true">
            <rect width="21" height="24" fill="var(--sky)"/>
            <path d="M6.5 7.5c.6-1 1.6-1.5 2.2-.8l1 1.6c.3.6 0 1-.5 1.4-.3.3-.2.7 0 1.1.7 1.2 1.6 2.1 2.8 2.8.4.2.8.3 1.1 0 .4-.5.8-.8 1.4-.5l1.6 1c.7.6.2 1.6-.8 2.2-1.3.8-3.4.1-5.6-2.1S5.7 8.8 6.5 7.5z" fill="#fff"/>
          </svg>
          <span>210-555-0147<br>210-555-0182</span>
        </li>
        <li class="contact__item">
          <svg class="contact__icon" viewBox="0 0 21 24" aria-hidden="true">
            <rect width="21" height="24" fill="var(--sky)"/>
            <circle cx="10.5" cy="12" r="5" fill="#fff"/>
            <path d="M8 9.5c1 .3 1.5 1 1.2 2-.3.8.5 1.3 1.2 1.6.5.4.2 1.2-.2 2M12 7.6c-.4.9.2 1.6 1 1.8.9.2 1.6.8 1.5 1.8" fill="none" stroke="var(--sky)" stroke-width="1"/>
          </svg>
          <span>reeves@rwholloway.com<br>www.rwholloway.com</span>
        </li>
      </ul>
    </div>
  </section>

  <section class="card card--back" aria-label="Business card back">
    <div class="back-brand">
      <span class="brand-square"></span>
      <span class="back-brand__name">RW HOLLOWAY LLC</span>
    </div>
  </section>
</main>
</body>
</html>
```